TalbeckLabs needs a new rocket based website

We need a new website that will be based on our rocket ship logo. We develop innovative solutions for enterprises. We would like to see a design that when the pages scroll, the rocket launches and goes from launch through a journey, similar to how we approach our customer. We would like areas for "Who are we", "What can we do", "What have we done", "How can we help". http://www.talbecklabs.example.au is our current website

Target Market(s)

Government, Enterprise, Cloud

Industry/Entity Type

Software Service

Coding

Coded - Design and coding required

Number of Pages Required

2 page

Requirements
Must have
• We would like to see a design that when the pages scroll, the rocket launches and goes from launch through a journey, similar to how we approach our customer.
• Must have a home page and a detail page.
• Would like to see the logo/rocket animate in some way when you scroll through he page.

```html
<!DOCTYPE html>
<html lang="en">
<head>
<meta charset="utf-8">
<title>TalbeckLabs</title>
<link href="https://fonts.googleapis.com/css2?family=Montserrat:wght@400;500;600;700&family=Raleway:wght@400;500;600&display=swap" rel="stylesheet">
<style>
:root{
  --orange:#f39019;
  --orange-deep:#e27a06;
  --orange-light:#f8b24a;
  --ink:#3a3a3a;
  --text:#5c5c5c;
  --slate:#3b4048;
  --slate-dark:#2b2f35;
  --footer:#3d3d3f;
  --field:#efefef;
  --white:#ffffff;
}
*{box-sizing:border-box;margin:0;padding:0}
html,body{width:1200px;height:4852px;overflow:hidden;background:var(--white)}
body{font-family:"Raleway",Arial,sans-serif;color:var(--text);position:relative}
.page{position:relative;width:1200px;height:4852px}
.abs{position:absolute}

/* hero */
.hero{position:absolute;left:0;top:0;width:1200px;height:1090px}
.hero-bg{position:absolute;inset:0}
.brand{position:absolute;left:48px;top:58px;font-family:"Montserrat",sans-serif;font-weight:700;font-size:38px;color:var(--white);display:flex;align-items:center;gap:12px}
.brand-dot{width:22px;height:22px;border-radius:50%;background:var(--white);flex:none}
.nav{position:absolute;right:40px;top:68px;display:flex;gap:46px}
.nav a{font-family:"Montserrat",sans-serif;font-weight:500;font-size:18px;color:var(--white);text-decoration:none}
.rocket-art{position:absolute;left:150px;top:30px;width:440px;height:1000px;border-radius:220px 220px 40px 40px;background:radial-gradient(ellipse at 50% 45%,rgba(255,248,230,.95) 0%,rgba(255,214,150,.7) 30%,rgba(255,180,80,0) 70%)}
.hero-title{position:absolute;left:556px;top:312px;font-family:"Montserrat",sans-serif;font-weight:700;font-size:37px;line-height:1.24;color:var(--white);white-space:nowrap}
.hero-sub{position:absolute;left:556px;top:552px;font-family:"Montserrat",sans-serif;font-size:26px;line-height:1.4;color:var(--white);white-space:nowrap}
.btn-outline{position:absolute;left:556px;top:652px;width:288px;height:58px;border:3px solid var(--white);border-radius:30px;color:var(--white);font-family:"Montserrat",sans-serif;font-weight:700;font-size:26px;display:flex;align-items:center;justify-content:center}

/* section headings */
.section-heading{position:absolute;left:0;width:1200px;text-align:center;font-family:"Montserrat",sans-serif;font-weight:600;font-size:35px;color:var(--ink);display:flex;justify-content:center;align-items:center;gap:16px}
.section-heading .accent{color:var(--orange)}
.section-heading .mark{width:20px;height:20px;border-radius:50%;background:var(--orange)}
.section-heading.light{color:var(--white)}

/* services */
.service-photo{position:absolute;width:320px;height:320px;border-radius:26px;border:10px solid var(--white);box-shadow:0 4px 22px rgba(0,0,0,.25)}
.service-title{position:absolute;font-family:"Montserrat",sans-serif;font-weight:500;font-size:33px;color:var(--orange);white-space:nowrap}
.service-text{position:absolute;width:410px;font-size:23px;line-height:1.45;color:var(--text)}

/* work */
.work{position:absolute;left:0;top:2680px;width:1200px;height:720px}
.work-card{position:absolute;top:2880px;width:316px;height:320px;border:3px solid rgba(255,255,255,.85);border-radius:16px;background:rgba(30,34,40,.45);padding:24px 22px;color:var(--white)}
.work-card h3{font-family:"Montserrat",sans-serif;font-weight:500;font-size:14px;text-transform:uppercase;letter-spacing:.2px;margin-bottom:34px;display:flex;align-items:center;gap:8px;white-space:nowrap;height:24px}
.work-card .seal{width:24px;height:24px;border-radius:50%;background:rgba(255,255,255,.8);flex:none}
.work-card p{font-size:19px;line-height:1.35}
.arrow{position:absolute;top:3008px;width:60px;height:60px;border-radius:50%;background:var(--orange)}

/* contact form */
.field{position:absolute;background:var(--field);font-family:"Montserrat",sans-serif;font-size:15px;color:var(--ink);padding:14px 14px}
.btn-send{position:absolute;left:480px;top:3815px;width:240px;height:48px;border-radius:24px;background:var(--orange);color:var(--white);font-family:"Montserrat",sans-serif;font-weight:600;font-size:24px;display:flex;align-items:center;justify-content:center}

/* footer */
.map{position:absolute;left:0;top:3945px;width:1200px;height:360px;background:linear-gradient(135deg,#e6e6e2,#dcdcd6 50%,#e9e7e0)}
.footer-brand{position:absolute;left:0;top:4432px;width:1200px;display:flex;justify-content:center;align-items:center;gap:12px;font-family:"Montserrat",sans-serif;font-weight:700;font-size:40px;color:var(--white)}
.foot-col{position:absolute;top:4555px;color:var(--white);font-family:"Montserrat",sans-serif}
.foot-col h4{font-size:16px;font-weight:600;text-transform:uppercase;padding-bottom:12px;border-bottom:2px solid rgba(255,255,255,.35);margin-bottom:16px;width:220px}
.foot-col ul{list-style:none}
.foot-col li{font-size:15px;line-height:1.6;display:flex;align-items:center;gap:10px}
.tri{width:0;height:0;border-left:8px solid var(--white);border-top:5px solid transparent;border-bottom:5px solid transparent}
.ico{width:22px;height:22px;border-radius:50%;border:2px solid var(--orange);flex:none}
.contact-item{display:flex;gap:12px;font-size:15px;line-height:1.4;margin-bottom:22px}
.news-text{font-size:15px;line-height:1.4;margin-bottom:14px;width:280px}
.news-input{width:258px;height:32px;border-radius:16px;background:var(--white);color:var(--ink);font-size:14px;padding:7px 16px;margin-bottom:12px}
.news-btn{width:128px;height:30px;border-radius:15px;background:var(--orange);font-size:13px;font-weight:700;display:flex;align-items:center;justify-content:center}
.bottom-bar{position:absolute;left:0;top:4805px;width:1200px;height:47px;background:var(--orange);display:flex;justify-content:space-between;align-items:center;padding:0 22px;color:var(--white);font-family:"Montserrat",sans-serif;font-size:12px;font-weight:600}
.socials{display:flex;gap:10px}
.socials span{width:20px;height:20px;border-radius:50%;background:var(--white)}
</style>
</head>
<body>
<div class="page">

  <!-- Hero -->
  <header class="hero">
    <svg class="hero-bg" width="1200" height="1090" viewBox="0 0 1200 1090" aria-hidden="true">
      <defs>
        <linearGradient id="heroGrad" x1="0" y1="0" x2="0" y2="1">
          <stop offset="0" stop-color="#f7a12c"/>
          <stop offset="1" stop-color="#ea8308"/>
        </linearGradient>
      </defs>
      <polygon points="0,0 1200,0 1200,975 600,1080 0,975" fill="url(#heroGrad)"/>
      <polyline points="0,990 600,1088 1200,990" fill="none" stroke="#e27a06" stroke-width="10"/>
    </svg>
    <div class="brand"><span class="brand-dot"></span>TalbeckLabs</div>
    <nav class="nav">
      <a href="#">Who Are We</a><a href="#">What Can We Do</a><a href="#">What Have We Done</a><a href="#">How Can We Help</a>
    </nav>
    <div class="rocket-art" role="img" aria-label="Glowing rocket lifting off above a bank of white clouds"></div>
    <h1 class="hero-title">Offering the latest in<br>enterprise architecture,<br>design and development<br>of bespoke software solutions</h1>
    <p class="hero-sub">Always researching and implementing<br>the latest technology for customers.</p>
    <div class="btn-outline">Get Started</div>
  </header>

  <!-- What can we do -->
  <h2 class="section-heading" style="top:1195px"><span class="mark"></span><span>What <span class="accent">Can We Do</span></span></h2>

  <div class="service-photo" style="left:140px;top:1292px;background:linear-gradient(135deg,#3a2a10,#c8892a 50%,#5a3a12)" role="img" aria-label="Golden digital tunnel of circuitry"></div>
  <h3 class="service-title" style="left:508px;top:1390px">e-Parliament</h3>
  <p class="service-text" style="left:508px;top:1450px">All of your Parliamentary software and business process needs.</p>

  <div class="service-photo" style="left:742px;top:1615px;background:linear-gradient(135deg,#1d2a10,#6a8a1c 50%,#1f2b12)" role="img" aria-label="Cloud computing icons over a glowing green background"></div>
  <h3 class="service-title" style="left:356px;top:1715px">Cloud</h3>
  <p class="service-text" style="left:356px;top:1775px;width:360px">Officeline 365, Migration, Security, Customisations.</p>

  <div class="service-photo" style="left:140px;top:1938px;background:linear-gradient(135deg,#3c4250,#9aa3b0 55%,#e5e7ea)" role="img" aria-label="Business team reviewing charts on a tablet"></div>
  <h3 class="service-title" style="left:508px;top:2037px">Architecture &amp; Design</h3>
  <p class="service-text" style="left:508px;top:2097px">Business process design, technology strategy and architecture.</p>

  <div class="service-photo" style="left:742px;top:2262px;background:linear-gradient(135deg,#2a1c08,#a87020 50%,#20160a)" role="img" aria-label="Hands working at a laptop with technology graphics"></div>
  <h3 class="service-title" style="left:326px;top:2362px">Software Development</h3>
  <p class="service-text" style="left:326px;top:2422px;width:370px">Software development including business apps, web and mobile.</p>

  <!-- What have we done -->
  <svg class="work" width="1200" height="720" viewBox="0 0 1200 720" role="img" aria-label="Dark slate background of a person using a touchscreen">
    <defs>
      <linearGradient id="workGrad" x1="0" y1="0" x2="1" y2="1">
        <stop offset="0" stop-color="#2d3139"/>
        <stop offset=".5" stop-color="#474d57"/>
        <stop offset="1" stop-color="#2b2f36"/>
      </linearGradient>
    </defs>
    <polygon points="0,0 1200,0 1200,590 600,695 0,590" fill="url(#workGrad)"/>
    <polyline points="0,600 600,708 1200,600" fill="none" stroke="#f39019" stroke-width="12"/>
  </svg>
  <h2 class="section-heading light" style="top:2783px"><span class="mark"></span><span><span class="accent">What</span> Have We Done</span></h2>

  <div class="work-card" style="left:90px"><h3><span class="seal"></span>Northmere Federal Assembly</h3><p>Lorem ipsum dolor sit amet, consectetur adipiscing elit, sed do eiusmod tempor incidi dunt ut labore et dolore magna aliqua. Lut enim ad minim veni am, quis nostrud exercitation ullamco laboris nisi ut aliquip.</p></div>
  <div class="work-card" style="left:443px"><h3>Eastvale State Council</h3><p>Lorem ipsum dolor sit amet, consectetur adipiscing elit, sed do eiusmod tempor incidi dunt ut labore et dolore magna aliqua. Lut enim ad minim veni am, quis nostrud exercitation ullamco laboris nisi ut aliquip.</p></div>
  <div class="work-card" style="left:796px"><h3>Office of Civic Affairs</h3><p>Lorem ipsum dolor sit amet, consectetur adipiscing elit, sed do eiusmod tempor incidi dunt ut labore et dolore magna aliqua. Lut enim ad minim veni am, quis nostrud exercitation ullamco laboris nisi ut aliquip.</p></div>

  <div class="arrow" style="left:-30px"></div>
  <svg class="abs" style="left:6px;top:3028px" width="14" height="20" viewBox="0 0 14 20" aria-hidden="true"><polyline points="11,2 3,10 11,18" fill="none" stroke="#fff" stroke-width="3"/></svg>
  <div class="arrow" style="left:1170px"></div>
  <svg class="abs" style="left:1180px;top:3028px" width="14" height="20" viewBox="0 0 14 20" aria-hidden="true"><polyline points="3,2 11,10 3,18" fill="none" stroke="#fff" stroke-width="3"/></svg>

  <!-- How can we help -->
  <h2 class="section-heading" style="top:3502px"><span class="mark"></span><span>How Can We Help</span></h2>
  <div class="field" style="left:113px;top:3605px;width:318px;height:50px">Your Name</div>
  <div class="field" style="left:443px;top:3605px;width:312px;height:50px">Your Email</div>
  <div class="field" style="left:770px;top:3605px;width:316px;height:50px">Your Subject</div>
  <div class="field" style="left:113px;top:3668px;width:973px;height:132px">Message</div>
  <div class="btn-send">Send</div>

  <!-- Map and footer -->
  <div class="map" role="img" aria-label="Street map showing the office location with a red pin"></div>
  <svg class="abs" style="left:0;top:4165px" width="1200" height="640" viewBox="0 0 1200 640" aria-hidden="true">
    <polygon points="0,0 600,110 1200,0 1200,640 0,640" fill="#3d3d3f"/>
    <polyline points="0,-8 600,102 1200,-8" fill="none" stroke="#f39019" stroke-width="16"/>
  </svg>
  <svg class="abs" style="left:586px;top:4062px" width="28" height="40" viewBox="0 0 28 40" aria-hidden="true"><path d="M14 2a12 12 0 0 1 12 12c0 9-12 24-12 24S2 23 2 14A12 12 0 0 1 14 2z" fill="#e03b2f"/><circle cx="14" cy="14" r="4.5" fill="#8d1c14"/></svg>

  <div class="footer-brand"><span class="brand-dot"></span>TalbeckLabs</div>

  <div class="foot-col" style="left:178px">
    <h4>Quick Links</h4>
    <ul>
      <li><span class="tri"></span>Who Are We</li>
      <li><span class="tri"></span>What Can We Do</li>
      <li><span class="tri"></span>What Have We Done</li>
      <li><span class="tri"></span>How Can We Help</li>
    </ul>
  </div>
  <div class="foot-col" style="left:453px">
    <h4>Contact</h4>
    <div class="contact-item"><span class="ico"></span><span>TalbeckLabs<br>Unit 3, 18 Kestrel Rd<br>Marden Vale, SA 5099</span></div>
    <div class="contact-item"><span class="ico"></span><span>1300 555 014</span></div>
    <div class="contact-item"><span class="ico"></span><span>info@talbecklabs.example.au</span></div>
  </div>
  <div class="foot-col" style="left:767px">
    <h4 style="width:280px">Newsletter Subscription</h4>
    <p class="news-text">Register your email address to get more information about us</p>
    <div class="news-input">Email Address</div>
    <div class="news-btn">SUBSCRIBE</div>
  </div>

  <div class="bottom-bar">
    <span>COPYRIGHT © 2018 TALBECKLABS. ALL RIGHTS RESERVED</span>
    <div class="socials"><span></span><span></span><span></span><span></span><span></span></div>
  </div>
</div>
</body>
</html>
```